business card - for laser marking

I need design (curve) for my business card (make with laser) size 85mm x 55mm. How it look business card with laser marking see attached picture.

color:
Background: white
text and icons black

Please include: one side
1. dominik vrabec - direktor
2. phone: +386(0)41 726 190
+386(0)580 237 61
3. info@zarezko.example
4. faecebook.com/Zarezko.Ex
5. KM-ATELJE, Dominik Vrabec s.p.
Lipova ulica 19, 1000 Ljubljana, SI
6. logo

Please include: second side
1. logo
2. www.zarezko.example
3. Lasersko graviranje
ovitki telefonov, ohišja telefonov / tablic, nakit, ure, alu vizitke, dog-tagi, kemični svinčniki, orodja, noži, vžigalniki

Industry/Entity Type

Business

Contact Information for Business Card

Please include: one side
+386(0)580 237 61
3. info@zarezko.example
6. logo

1. logo
2. www.zarezko.example
3. Lasersko graviranje

Colors
000000
ffffff

Requirements
Must have
• I need design (curve) for my business card (make with laser) size 85mm x 55mm. How it look business card with laser marking see attached picture.
• color:
• Background: white
• text and icons black
• Please include: one side
• 1. dominik vrabec - direktor
• 2. phone: +386(0)41 726 190
• +386(0)580 237 61
• 3. info@zarezko.example
• 4. faecebook.com/Zarezko.Ex
• 5. KM-ATELJE, Dominik Vrabec s.p.
• Lipova ulica 19, 1000 Ljubljana, SI
• 6. logo
• Please include: second side
• 1. logo
• 2. www.zarezko.example
• 3. Lasersko graviranje
• ovitki telefonov, ohišja telefonov / tablic, nakit, ure, alu vizitke, dog-tagi, kemični svinčniki, orodja, noži, vžigalniki

```html
<!DOCTYPE html>
<html lang="sl">
<head>
<meta charset="utf-8">
<title>Zarezko – vizitka</title>
<link href="https://fonts.googleapis.com/css2?family=Roboto:wght@400;500;700&family=Roboto+Condensed:wght@700&display=swap" rel="stylesheet">
<style>
  :root {
    --stage: #ecebe8;
    --paper: #f7f7f6;
    --crimson: #c8134a;
    --leaf: #5e9b2e;
    --ink: #4a4a4a;
    --rule: #c9c9c9;
    --white: #ffffff;
  }
  * { margin: 0; padding: 0; box-sizing: border-box; }
  html, body {
    width: 1200px; height: 960px; overflow: hidden;
    background: var(--stage);
    font-family: "Roboto", Arial, sans-serif;
  }
  .canvas { position: relative; width: 1200px; height: 960px; }

  /* front side */
  .card-front {
    position: absolute; left: 314px; top: 113px; width: 600px; height: 343px;
    background: var(--paper);
    box-shadow: 0 2px 6px rgba(0,0,0,.25);
  }
  .card-front .base-band {
    position: absolute; left: 0; right: 0; bottom: 0; height: 13px;
    background: var(--crimson);
  }
  .card-front .base-line {
    position: absolute; left: 0; right: 0; bottom: 16px; height: 2px;
    background: var(--leaf);
  }
  .brand {
    position: absolute; display: flex; align-items: center; gap: 10px;
    font-family: "Roboto", Arial, sans-serif; font-weight: 700;
    letter-spacing: 1px;
  }
  .brand .dot { border-radius: 50%; flex: none; }
  .card-front .brand {
    left: 70px; top: 170px; font-size: 30px; color: var(--crimson);
  }
  .card-front .brand .dot { width: 18px; height: 18px; background: var(--leaf); }
  .divider {
    position: absolute; left: 321px; top: 72px; width: 1px; height: 215px;
    background: var(--rule);
  }
  .contact { position: absolute; left: 354px; top: 68px; color: var(--ink); }
  .contact .name {
    font-family: "Roboto Condensed", Arial, sans-serif; font-weight: 700;
    font-size: 22px; color: var(--crimson); line-height: 26px;
  }
  .contact .role {
    font-family: "Roboto Condensed", Arial, sans-serif; font-weight: 700;
    font-size: 15px; color: var(--leaf); margin-top: 2px; letter-spacing: .3px;
  }
  .contact .address { margin-top: 10px; font-size: 14px; line-height: 18px; }
  .contact .channels { margin-top: 8px; font-size: 14px; line-height: 19px; list-style: none; }
  .contact .channels li { display: flex; align-items: center; gap: 9px; }
  .contact .channels svg { width: 12px; height: 12px; flex: none; }

  /* back side */
  .card-back {
    position: absolute; left: 311px; top: 472px; width: 600px; height: 343px;
    background: var(--crimson); color: var(--white); text-align: center;
    box-shadow: 0 2px 6px rgba(0,0,0,.25);
  }
  .card-back .brand {
    left: 50%; top: 125px; transform: translateX(-50%);
    font-size: 30px; color: var(--white);
  }
  .card-back .brand .dot { width: 18px; height: 18px; background: var(--white); }
  .services { position: absolute; left: 0; right: 0; top: 241px; font-size: 14px; line-height: 18px; }
  .website { position: absolute; left: 0; right: 0; top: 302px; font-size: 16px; font-weight: 500; }
</style>
</head>
<body>
<main class="canvas">

  <section class="card-front" aria-label="Sprednja stran vizitke">
    <div class="brand"><span class="dot"></span><span>ZAREZKO</span></div>
    <div class="divider"></div>
    <div class="contact">
      <div class="name">DOMINIK VRABEC</div>
      <div class="role">DIREKTOR</div>
      <div class="address">
        KM-ATELJE<br>
        Dominik Vrabec s.p.<br>
        Lipova ulica 19<br>
        1000 Ljubljana, SI
      </div>
      <ul class="channels">
        <li>
          <svg viewBox="0 0 12 12" aria-hidden="true"><path fill="#c8134a" d="M2.4 0.6l2 2.2-1 1.4c.8 1.7 2 2.9 3.5 3.6l1.4-1 2.1 2-1 2C6 10.8 1.3 6 .6 1.6z"/></svg>
          <span>+386(0)580 237 61</span>
        </li>
        <li>
          <svg viewBox="0 0 12 12" aria-hidden="true"><rect x="2.5" y="0.5" width="7" height="11" rx="1.2" fill="none" stroke="#c8134a" stroke-width="1.4"/><circle cx="6" cy="9.4" r=".8" fill="#c8134a"/></svg>
          <span>+386(0)41 726 190</span>
        </li>
        <li>
          <svg viewBox="0 0 12 12" aria-hidden="true"><rect x="0.5" y="2.5" width="11" height="7.5" fill="#c8134a"/><path d="M0.8 2.8L6 6.8l5.2-4" fill="none" stroke="#f7f7f6" stroke-width="1"/></svg>
          <span>info@zarezko.example</span>
        </li>
        <li>
          <svg viewBox="0 0 12 12" aria-hidden="true"><rect x="0.5" y="0.5" width="11" height="11" fill="#c8134a"/></svg>
          <span>Zarezko.Ex</span>
        </li>
      </ul>
    </div>
    <div class="base-line"></div>
    <div class="base-band"></div>
  </section>

  <section class="card-back" aria-label="Zadnja stran vizitke">
    <div class="brand"><span class="dot"></span><span>ZAREZKO</span></div>
    <p class="services">
      Lasersko graviranje<br>
      ovitki telefonov, ohišja telefonov / tablic, nakit, ure, alu vizitke<br>
      dog-tagi, kemicni svincniki, orodja, noži, vžigalniki
    </p>
    <p class="website">www.zarezko.example</p>
  </section>

</main>
</body>
</html>
```